ONE PAGE WEBSITE for Zesty Recruitment Agency

Hello creative gurus,

We're are after a ONE PAGE World Press web design.

We're a recruitment start-up specializing in Information Technology.

The design should be cool, quirky and NOT mainstream.

The kind of web designs we like:

http://www.vantorix.co.za/#what-we-do
http://quillandmoss.com/
http://www.kelvado.com/index.html#home
http://marcellobrantovi.com/#/selected-works

And, we only like the front page of this web site: http://www.zenbyglim.com/

Any questions, please do let us know!

Thank you, and happy creating!

Robin

Reason: Just need a day or two to finalize everything. Thanks, Robin

Target Market(s)

Companies, employees, candidates

Industry/Entity Type

Recruitment

Coding

Coded - Design and coding required

Colors
f37122
f68e4e
ffcf3e
00a990
86cfc6
fcca95
fee18a

Requirements
Must have
• 1. The website should be techy, cool, funky, quirky and user-friendly.
• 2. Mobile-compatible
• 3. Please use our spaceman logo through the website (attached).
• 4. Please see attached website content/brief.
• 5. Colors - orange color is a must, but please use other colors to spice it up - make it more fun.
• The kind of web designs we like:
• http://www.vantorix.co.za/#what-we-do
• http://quillandmoss.com/
• http://www.kelvado.com/index.html#home
• http://marcellobrantovi.com/#/selected-works
• http://www.zenbyglim.com/
• Any questions, please do let us know!
Should not have
• -NO stock image banners, photos, images

```html
<!DOCTYPE html>
<html lang="en">
<head>
<meta charset="utf-8">
<title>VeltroTalent – IT Recruitment</title>
<link rel="stylesheet" href="https://fonts.googleapis.com/css2?family=Montserrat:wght@400;500&family=Open+Sans:wght@400&display=swap">
<style>
  :root {
    --orange: #f37122;
    --ink: #222222;
    --text: #666666;
    --muted: #9a9a9a;
    --border: #666666;
    --bg: #ffffff;
    --skyline-light: #b4c6d2;
    --skyline-mid: #5d8196;
  }
  * { box-sizing: border-box; margin: 0; padding: 0; }
  html, body { width: 1200px; height: 1161px; overflow: hidden; background: var(--bg); }
  body { position: relative; font-family: "Open Sans", Arial, sans-serif; color: var(--text); }

  .brand { position: absolute; left: 132px; top: 26px; display: flex; align-items: flex-end; gap: 4px; text-decoration: none; }
  .brand-mark { width: 46px; height: 46px; border-radius: 50%; background: var(--ink); }
  .brand-name { font-family: "Montserrat", Arial, sans-serif; font-weight: 500; font-size: 20px; letter-spacing: 2px; color: var(--ink); line-height: 1; margin-bottom: -2px; }

  .main-nav { position: absolute; top: 67px; left: 379px; width: 692px; display: flex; justify-content: space-between; }
  .main-nav a { font-family: "Montserrat", Arial, sans-serif; font-size: 11px; letter-spacing: 1.3px; color: #555; text-decoration: none; text-transform: uppercase; }
  .main-nav a.is-active { color: var(--orange); }

  .hero-kicker { position: absolute; left: 133px; top: 192px; font-family: "Montserrat", Arial, sans-serif; font-size: 18px; letter-spacing: 2.5px; color: var(--ink); font-weight: 400; }
  .hero-title { position: absolute; left: 130px; top: 230px; font-family: "Montserrat", Arial, sans-serif; font-size: 37px; letter-spacing: 4.4px; color: var(--orange); font-weight: 400; }
  .hero-lead { position: absolute; left: 133px; top: 302px; width: 346px; font-size: 11px; line-height: 24px; text-align: justify; text-align-last: left; }
  .btn-outline { position: absolute; left: 132px; top: 376px; width: 117px; height: 41px; border: 2px solid var(--border); display: flex; align-items: center; justify-content: center; font-family: "Montserrat", Arial, sans-serif; font-size: 13px; letter-spacing: 1.6px; color: var(--ink); text-decoration: none; }

  .hero-art { position: absolute; left: 532px; top: 124px; width: 442px; height: 408px; border-radius: 6px;
    background: linear-gradient(90deg, #f1e6e8 0%, #eef2e2 35%, var(--skyline-light) 70%, var(--skyline-mid) 100%); }
  .hero-art-small { position: absolute; left: 476px; top: 368px; width: 68px; height: 110px; border-radius: 4px;
    background: linear-gradient(180deg, var(--skyline-light), var(--skyline-mid)); }

  .section-title { position: absolute; top: 596px; left: 0; width: 1200px; text-align: center; font-family: "Montserrat", Arial, sans-serif; font-weight: 400; font-size: 28px; letter-spacing: 4.5px; color: var(--ink); }

  .feature-icon { position: absolute; }
  .feature-text { position: absolute; width: 361px; font-size: 10.8px; line-height: 24px; text-align: justify; text-align-last: left; }
  .icon-a { left: 134px; top: 690px; } .text-a { left: 202px; top: 692px; }
  .icon-b { left: 638px; top: 694px; } .text-b { left: 706px; top: 692px; }
  .icon-c { left: 134px; top: 792px; } .text-c { left: 202px; top: 796px; }
  .icon-d { left: 644px; top: 790px; } .text-d { left: 706px; top: 796px; }

  .closing { position: absolute; top: 930px; left: 120px; width: 960px; text-align: center; font-family: "Montserrat", Arial, sans-serif; font-size: 10.8px; line-height: 24px; letter-spacing: 0.9px; color: var(--ink); text-transform: uppercase; }
  .callout { position: absolute; top: 1014px; left: 0; width: 1200px; text-align: center; font-family: "Montserrat", Arial, sans-serif; font-size: 18px; letter-spacing: 1.8px; color: var(--ink); text-transform: uppercase; }

  .social { position: absolute; top: 1073px; left: 0; width: 1200px; display: flex; justify-content: center; align-items: center; gap: 14px; }
  .social-dot { width: 16px; height: 16px; border-radius: 50%; background: var(--muted); }
  .legal { position: absolute; top: 1116px; left: 0; width: 1200px; text-align: center; font-family: "Montserrat", Arial, sans-serif; font-size: 9.5px; color: var(--ink); text-transform: uppercase; }
</style>
</head>
<body>
  <header>
    <a class="brand" href="#home" aria-label="Veltro">
      <span class="brand-mark"></span>
      <span class="brand-name">VELTRO</span>
    </a>
    <nav class="main-nav">
      <a class="is-active" href="#home">Home</a>
      <a href="#companies">Companies</a>
      <a href="#talent">Talent</a>
      <a href="#referals">Referals</a>
      <a href="#about">About us</a>
      <a href="#blog">Blog</a>
      <a href="#contact">Contact us</a>
    </nav>
  </header>

  <section id="home" class="hero">
    <h2 class="hero-kicker">WELCOME TO</h2>
    <h1 class="hero-title">VELTROTALENT</h1>
    <p class="hero-lead">We specialise in permanent and contract recruitment solutions across Information Technology.</p>
    <a class="btn-outline" href="#about">READ MORE</a>
    <div class="hero-art-small" role="img" aria-label="Small stylised skyscrapers"></div>
    <div class="hero-art" role="img" aria-label="Illustration of a young woman and man standing in front of stylised city skyscrapers"></div>
  </section>

  <section class="why">
    <h2 class="section-title">WHY WORK WITH US?</h2>

    <svg class="feature-icon icon-a" width="42" height="40" viewBox="0 0 42 40" fill="none" stroke="#f37122" stroke-width="1.5">
      <rect x="1" y="6" width="40" height="33"/><line x1="1" y1="12" x2="41" y2="12"/>
      <rect x="18" y="1" width="6" height="6"/>
      <circle cx="13" cy="21" r="4"/><path d="M6 33c0-5 3-7 7-7s7 2 7 7"/>
      <line x1="25" y1="19" x2="36" y2="19"/><line x1="25" y1="24" x2="36" y2="24"/><line x1="25" y1="29" x2="36" y2="29"/>
    </svg>
    <p class="feature-text text-a">We’re experts in our field and have years ofhands-on experience in the I.T. industry.We know our market intimately and understand the unique skills required to build a successful I.T. team.</p>

    <svg class="feature-icon icon-b" width="44" height="34" viewBox="0 0 44 34" fill="none" stroke="#f37122" stroke-width="1.5">
      <circle cx="14" cy="9" r="7"/><path d="M1 30c0-8 5-11 13-11s13 3 13 11z"/>
      <circle cx="29" cy="9" r="7"/><path d="M22 33h21c0-8-5-12-13-12"/>
    </svg>
    <p class="feature-text text-b">We walk in your shoes. We’ve been on the other side of the recruitment process - your side (wether you’re a talent or an employer), and we understand the challenges you’re facing.</p>

    <svg class="feature-icon icon-c" width="30" height="46" viewBox="0 0 30 46" fill="none" stroke="#f37122" stroke-width="1.5">
      <path d="M6 1h18v10l-5 10h-8L6 11z"/><line x1="12" y1="1" x2="12" y2="20"/><line x1="18" y1="1" x2="18" y2="20"/>
      <circle cx="15" cy="31" r="13"/><circle cx="15" cy="31" r="8"/>
    </svg>
    <p class="feature-text text-c">We offer a bespoke service with dedicated account manager (a nice one!) who will stay in regular contact with you.</p>

    <svg class="feature-icon icon-d" width="34" height="48" viewBox="0 0 34 48" fill="none" stroke="#f37122" stroke-width="1.5">
      <path d="M11 34c0-6-10-10-10-19a16 16 0 0 1 32 0c0 9-10 13-10 19z"/>
      <rect x="11" y="34" width="12" height="12"/><line x1="11" y1="40" x2="23" y2="40"/>
      <line x1="17" y1="34" x2="17" y2="20"/><circle cx="17" cy="17" r="3"/>
    </svg>
    <p class="feature-text text-d">We’re nice. We’re ethical. &nbsp;We’ll even bring you your favourite coffee, hot chocolate, beer (whatever makes you tick) when we come to meet you!</p>
  </section>

  <footer id="contact">
    <p class="closing">Whether you’re a client looking to fill a vacancy, or a candidate searching for your next move, we can help you.We’re a friendly bunch and we’d be happy to chat to you about working together.</p>
    <p class="callout">Call us on 0207 555 0186 or say “hello” at info@veltrotalent.com</p>
    <div class="social">
      <svg width="20" height="16" viewBox="0 0 20 16" fill="none" stroke="#9a9a9a" stroke-width="1.5" aria-label="Email">
        <rect x="1" y="1" width="18" height="14" rx="1"/><path d="M1 2l9 7 9-7"/>
      </svg>
      <span class="social-dot" aria-label="Professional network"></span>
      <span class="social-dot" aria-label="Social network"></span>
    </div>
    <p class="legal">©2017 veltrotalent.com. All right reserved.</p>
  </footer>
</body>
</html>
```